Business Folder

I need a fresh, modern design for a business folder. I have our company's colors, logo, and a separate file for just the graphic part of our logo as a design element. No photo, just colors, gradients, and shadows to create depth. I like the idea of a rich grey as the background, however, I realize we'd have to lighten to 'Tax Advisory Services' part of our logo.

The design would just be the 'front' or outside of the folder from PressVale. Design file attached. You can find that here under 9 x 12 standard folder, Left and Right Pockets With Slit Both Sides:

https://www.pressvale-example.com/content.html?id=folderDownloadTemplates&rightMenuId=rightMenu&footerId=bodyFooterStyle6

```html
<!DOCTYPE html>
<html lang="en">
<head>
<meta charset="utf-8">
<title>Keene Tax Advisory Services – Presentation Folder</title>
<link href="https://fonts.googleapis.com/css2?family=Montserrat:wght@300;500;600;800&display=swap" rel="stylesheet">
<style>
  :root {
    --stage: #8a8a8a;
    --brand-blue: #0f5082;
    --brand-blue-light: #1f5d8d;
    --ink-grey: #555a5e;
    --paper: #ffffff;
    --paper-grey: #e4e4e6;
    --pocket-grey: #d9dadc;
    --watermark: rgba(15, 80, 130, 0.07);
  }
  * { box-sizing: border-box; margin: 0; padding: 0; }
  html, body { width: 1200px; height: 1200px; overflow: hidden; }
  body {
    background: var(--stage);
    font-family: "Montserrat", sans-serif;
    position: relative;
  }
  .panel {
    position: absolute;
    width: 360px;
    height: 480px;
    overflow: hidden;
    box-shadow: 0 6px 18px rgba(0,0,0,0.28);
  }

  /* Front cover */
  .front-cover {
    left: 210px; top: 50px;
    background: linear-gradient(160deg, #dcdcde 0%, #f2f2f3 45%, #ffffff 70%, #ececed 100%);
  }
  .front-cover .texture {
    position: absolute; inset: 0 0 50% 0;
    background: linear-gradient(180deg, rgba(255,255,255,0.25), rgba(255,255,255,0));
  }
  .brand-mark {
    position: absolute;
    color: var(--brand-blue);
    font-weight: 800;
    line-height: 1;
    text-transform: uppercase;
  }
  .brand-mark .brand-sub {
    display: block;
    font-size: 0.24em;
    letter-spacing: 0.12em;
    margin-top: 0.25em;
  }
  .front-cover .brand-mark { left: 110px; top: 66px; font-size: 40px; }
  .headline-lead {
    position: absolute; left: 0; right: 0; top: 178px;
    text-align: center;
    font-weight: 300;
    font-size: 27px;
    letter-spacing: 0.02em;
    color: var(--ink-grey);
  }
  .headline-band {
    position: absolute; left: 32px; right: 32px; top: 214px;
    background: var(--brand-blue);
    color: var(--paper);
    text-align: center;
    font-weight: 800;
    font-size: 38px;
    letter-spacing: 0.03em;
    padding: 6px 0 5px;
  }
  .headline-tag {
    position: absolute; left: 0; right: 0; top: 276px;
    text-align: center;
    font-weight: 600;
    font-size: 13px;
    color: var(--brand-blue);
  }
  .front-cover .web {
    position: absolute; right: 28px; bottom: 34px;
    font-size: 10px; font-weight: 500; color: #333;
  }

  /* Back cover */
  .back-cover {
    left: 630px; top: 50px;
    background: var(--brand-blue);
  }
  .back-cover .decor {
    position: absolute; left: 20px; top: 40px; width: 320px; height: 340px;
    background: radial-gradient(ellipse at 55% 45%, rgba(255,255,255,0.08), rgba(255,255,255,0) 70%);
  }
  .back-cover .web {
    position: absolute; left: 0; right: 0; bottom: 52px;
    text-align: center;
    font-size: 11px; font-weight: 500; color: var(--paper);
  }

  /* Inside spread */
  .inside-spread {
    position: absolute; left: 240px; top: 600px;
    width: 720px; height: 480px;
    box-shadow: 0 6px 18px rgba(0,0,0,0.28);
    overflow: hidden;
  }
  .inside-left, .inside-right {
    position: absolute; top: 0; width: 360px; height: 480px;
  }
  .inside-left { left: 0; background: var(--paper); }
  .inside-right {
    left: 360px;
    background: linear-gradient(90deg, #b5b5b7 0%, #e2e2e3 35%, #ffffff 75%);
  }
  .watermark {
    position: absolute; top: 200px; left: 0; right: 0;
    text-align: center;
    color: var(--watermark);
    font-weight: 800;
    font-size: 60px;
    line-height: 1;
    text-transform: uppercase;
  }
  .watermark .brand-sub { display: block; font-size: 14px; letter-spacing: 0.14em; margin-top: 6px; }
  .pockets { position: absolute; left: 0; top: 0; }
  .pocket-web {
    position: absolute; left: 0; width: 340px; top: 392px;
    text-align: center;
    font-size: 15px; font-weight: 600; color: var(--paper);
  }
  .inside-spread .brand-mark { left: 470px; top: 372px; font-size: 46px; }
</style>
</head>
<body>

  <section class="panel front-cover" aria-label="Folder front cover">
    <div class="texture" role="img" aria-label="Soft light grey geometric background texture"></div>
    <div class="brand-mark">Keene<span class="brand-sub">Tax Advisory Services</span></div>
    <p class="headline-lead">COMMITTED TO</p>
    <p class="headline-band">SOLUTIONS</p>
    <p class="headline-tag">A Present And Future Business Service</p>
    <p class="web">www.keenetaxadvisory.com</p>
  </section>

  <section class="panel back-cover" aria-label="Folder back cover">
    <div class="decor" role="img" aria-label="Large faint brand graphic decoration"></div>
    <p class="web">www.keenetaxadvisory.com</p>
  </section>

  <section class="inside-spread" aria-label="Folder inside with pockets">
    <div class="inside-left">
      <div class="watermark">Keene<span class="brand-sub">Tax Advisory Services</span></div>
    </div>
    <div class="inside-right">
      <div class="watermark">Keene<span class="brand-sub">Tax Advisory Services</span></div>
    </div>
    <svg class="pockets" width="720" height="480" viewBox="0 0 720 480">
      <path class="pocket-left" d="M0 338 H340 Q352 338 353 350 L358 480 H0 Z" fill="#0f5082"/>
      <path class="pocket-right" d="M374 344 Q378 340 386 340 H720 V480 H362 Z" fill="#d9dadc"/>
    </svg>
    <p class="pocket-web">www.keenetaxadvisory.com</p>
    <div class="brand-mark">Keene<span class="brand-sub">Tax Advisory Services</span></div>
  </section>

</body>
</html>
```